SkyvornQ Business Cards and Stationary Design

Need a design for our business cards and stationary. I want to carry on the theme of the logo. I want the business cards to have a design on the back. I would like the business cards and the stationary to carry the same theme, design scheme, and branding

Target Market(s)

Airlines and Maintenance Facilities

Industry/Entity Type

Aviation

Contact Information for Business Card

Name
Position Title
Address: 4827 Trellis Hollow Road, Marlow Springs, Oregon, 97512
Office Number
Mobile Number
Email
Website

Font styles to use
Serif
Sans Serif

Colors

Designer to choose colors to be used in the design.

```html
<!DOCTYPE html>
<html lang="en">
<head>
<meta charset="utf-8">
<title>SkyvornQ Business Card</title>
<link href="https://fonts.googleapis.com/css2?family=Open+Sans:wght@400;600;700&display=swap" rel="stylesheet">
<style>
  :root {
    --navy: #0b2850;
    --accent: #1a7fcf;
    --card: #f7f7f6;
    --backdrop: #e6e6e4;
    --ink-light: #ffffff;
  }
  html, body {
    margin: 0;
    width: 1200px;
    height: 900px;
    overflow: hidden;
    background: var(--backdrop);
    font-family: "Open Sans", Arial, sans-serif;
  }
  .business-card {
    position: absolute;
    left: 150px;
    top: 170px;
    width: 900px;
    height: 559px;
    background: var(--card);
    overflow: hidden;
    box-shadow: 0 10px 30px rgba(0,0,0,0.12);
  }
  .card-shape {
    position: absolute;
    inset: 0;
  }
  .contact-block {
    position: absolute;
    left: 46px;
    top: 205px;
    color: var(--ink-light);
  }
  .person-name {
    margin: 0;
    font-size: 28px;
    font-weight: 700;
    letter-spacing: 0.3px;
    line-height: 1.15;
  }
  .person-title {
    margin: 0 0 26px;
    font-size: 25px;
    font-weight: 400;
    line-height: 1.3;
  }
  .contact-list {
    list-style: none;
    margin: 0 0 14px;
    padding: 0;
  }
  .contact-list li {
    display: flex;
    align-items: center;
    gap: 8px;
    font-size: 25px;
    line-height: 33px;
  }
  .contact-list svg {
    width: 20px;
    height: 20px;
    fill: var(--ink-light);
    flex: none;
  }
  .address {
    font-style: normal;
    font-size: 25px;
    line-height: 32px;
  }
  .brand {
    position: absolute;
    left: 665px;
    top: 66px;
    transform: translateX(-50%);
    display: flex;
    flex-direction: column;
    align-items: center;
  }
  .brand-circle {
    width: 124px;
    height: 124px;
    border-radius: 50%;
    border: 7px solid var(--accent);
    box-sizing: border-box;
  }
  .brand-name {
    margin-top: 22px;
    font-size: 44px;
    font-weight: 700;
    letter-spacing: 5px;
    color: var(--navy);
    white-space: nowrap;
  }
</style>
</head>
<body>
  <article class="business-card">
    <svg class="card-shape" viewBox="0 0 900 559" width="900" height="559" aria-hidden="true">
      <path d="M0,0 L30,0 C255,8 405,140 492,268 L682,559 L0,559 Z" fill="var(--accent)"/>
      <path d="M0,0 C230,5 382,140 470,270 L662,559 L0,559 Z" fill="var(--navy)"/>
    </svg>

    <div class="contact-block">
      <h1 class="person-name">MARCUS ELLERY</h1>
      <p class="person-title">Managing Director</p>
      <ul class="contact-list">
        <li>
          <svg viewBox="0 0 20 20"><path d="M3 7c0-2 2-3 7-3s7 1 7 3v1h-4V6.5H7V8H3z M5 9h10l2 7H3z M10 10.5a2 2 0 1 0 0 4a2 2 0 0 0 0-4z"/></svg>
          044-987 654 321
        </li>
        <li>
          <svg viewBox="0 0 20 20"><path d="M6 1h8a1 1 0 0 1 1 1v16a1 1 0 0 1-1 1H6a1 1 0 0 1-1-1V2a1 1 0 0 1 1-1zm1 3v10h6V4zm3 11.5a1 1 0 1 0 0 2a1 1 0 0 0 0-2z"/></svg>
          044-987 654 321
        </li>
        <li>
          <svg viewBox="0 0 20 20"><path d="M2 5h16v10H2z M3 6l7 5 7-5" stroke="var(--navy)" stroke-width="1.4" fill="var(--ink-light)"/></svg>
          info@skyvornq.com
        </li>
        <li>
          <svg viewBox="0 0 20 20"><circle cx="10" cy="10" r="8"/><path d="M6 7c2 0 3 1 2 3s1 3 0 5M13 4c-1 2 1 3 3 3M12 13c1-1 3 0 3 2" stroke="var(--navy)" stroke-width="1.5" fill="none"/></svg>
          www.skyvornq.com
        </li>
      </ul>
      <address class="address">4827 Trellis Hollow Road<br>Marlow Springs, Oregon, 97512</address>
    </div>

    <div class="brand">
      <div class="brand-circle"></div>
      <div class="brand-name">SKYVORNQ</div>
    </div>
  </article>
</body>
</html>
```